Local fast-growing company in the service sector

We are looking for a modern business card design, which should also appear on our letterheads

Target Market(s)

Private and industrial sectors

Contact Information for Business Card

Vorname Name
Kellberger Str. 18
71486 Lindenau
Tel.: 07146-839214-0
Name@agentur-kvtl.de

Colors
9d9d9d
919191
aaaaaa

Requirements
Must have
• The logo (file) in silver

```html
<!DOCTYPE html>
<html lang="de">
<head>
<meta charset="utf-8">
<title>KVTL – Visitenkarte</title>
<link rel="stylesheet" href="https://fonts.googleapis.com/css2?family=Roboto:wght@400;500&family=Roboto+Condensed:wght@400&display=swap">
<style>
  :root {
    --backdrop: #2b2b2b;
    --silver-dark: #7a7a7a;
    --silver-mid: #9d9d9d;
    --silver-light: #d4d4d4;
    --paper: #ffffff;
    --brand-grey: #919191;
    --ink-light: #ffffff;
  }
  * { margin: 0; padding: 0; box-sizing: border-box; }
  html, body { width: 1200px; height: 960px; overflow: hidden; }
  body {
    background: var(--backdrop);
    font-family: "Roboto", Arial, sans-serif;
    position: relative;
  }
  .card {
    position: absolute;
    width: 600px;
    height: 342px;
    overflow: hidden;
    box-shadow: 0 3px 10px rgba(0,0,0,.55);
  }
  .card-front {
    left: 314px; top: 113px;
    background: radial-gradient(ellipse 70% 75% at 38% 55%, var(--silver-light) 0%, var(--silver-mid) 55%, var(--silver-dark) 100%);
  }
  .card-back {
    left: 311px; top: 472px;
    background: radial-gradient(ellipse 60% 70% at 50% 42%, var(--silver-light) 0%, var(--silver-mid) 55%, var(--silver-dark) 100%);
  }
  .front-shape { position: absolute; inset: 0; }
  .holder-name {
    position: absolute; left: 46px; top: 45px;
    font-family: "Roboto Condensed", "Arial Narrow", sans-serif;
    font-weight: 400; font-size: 21px; color: var(--ink-light);
  }
  .address {
    position: absolute; left: 46px; top: 75px;
    font-size: 14px; line-height: 19px; color: var(--ink-light);
  }
  .contacts {
    position: absolute; left: 47px; top: 249px;
    list-style: none; font-size: 14px; line-height: 19.5px; color: var(--ink-light);
  }
  .contacts li { display: flex; align-items: center; gap: 8px; }
  .contacts svg { width: 13px; height: 13px; fill: var(--ink-light); flex: none; }
  .brand {
    position: absolute; display: flex; align-items: center; gap: 12px;
    font-family: "Roboto", Arial, sans-serif; font-weight: 500; letter-spacing: 2px;
  }
  .brand-front { left: 326px; top: 150px; color: var(--brand-grey); font-size: 46px; }
  .brand-front .brand-mark { width: 30px; height: 30px; background: var(--brand-grey); }
  .brand-back { left: 150px; top: 140px; color: var(--ink-light); font-size: 64px; }
  .brand-back .brand-mark { width: 42px; height: 42px; background: var(--ink-light); }
  .back-url {
    position: absolute; left: 0; right: 0; top: 286px; text-align: center;
    font-size: 15px; letter-spacing: 6.5px; color: var(--ink-light);
  }
</style>
</head>
<body>
  <section class="card card-front">
    <svg class="front-shape" viewBox="0 0 600 342" width="600" height="342" aria-hidden="true">
      <defs>
        <linearGradient id="band-shade" x1="0" y1="0" x2="1" y2="0">
          <stop offset="0" stop-color="#bdbdbd"/>
          <stop offset="1" stop-color="#e6e6e6"/>
        </linearGradient>
      </defs>
      <path d="M376 0 L210 155 Q195 171 210 187 L376 342 L600 342 L600 0 Z" fill="url(#band-shade)"/>
      <path d="M416 0 L255 155 Q240 171 255 187 L416 342 L600 342 L600 0 Z" fill="var(--paper)"/>
    </svg>
    <h1 class="holder-name">VORNAME NAME</h1>
    <p class="address">Kellberger Str. 18<br>71486 Lindenau</p>
    <ul class="contacts">
      <li><svg viewBox="0 0 16 16"><path d="M3 1l3 3-1.5 2a9 9 0 0 0 5.5 5.5L12 10l3 3-2 2C7 15 1 9 1 3z"/></svg>07146-839214-0</li>
      <li><svg viewBox="0 0 16 16"><path d="M1 3h14v1.5L8 9 1 4.5z M1 6.5l7 4.5 7-4.5V13H1z"/></svg>Name@agentur-kvtl.de</li>
      <li><svg viewBox="0 0 16 16"><circle cx="8" cy="8" r="7"/><path d="M4 5l3 1-1 3 3 1v3M10 3l1 3 3 1" stroke="#9d9d9d" stroke-width="1.2" fill="none"/></svg>www.agentur-kvtl.de</li>
    </ul>
    <div class="brand brand-front"><span class="brand-mark"></span>KVTL</div>
  </section>

  <section class="card card-back">
    <div class="brand brand-back"><span class="brand-mark"></span>KVTL</div>
    <p class="back-url">www.agentur-kvtl.de</p>
  </section>
</body>
</html>
```